RW Holloway LLC Business Card - Civil Engineering & Consulting Firm

We need a Business Card that is elegant, and masculine.  It is our Professional Civil Engineering & Consulting Company located in San Antonio TX (Not s construction or builder firm- no gears & no tool images please). We provide civil engineering services including  commercial site plans, grading and drainage plans, utility plans, hydraulics and hydrology, land planning, utility coordination, and other general civil engineering services related to commercial and residential development.
We have 2 existing Logos. We would like to convey reliability, strength, trustworthiness and attention to detail.  Blues and orange tones as per logo We are OK with the use of a darker blue in the mix.  We have 2 logo versions - Full Company Name Logo to go on the back of card, & Small Icon Logo for the front w/ personal Info.

Target Market(s)
Architects, Real Estate Developers, Other Strctural Engineers, Surveyers, General Contractors
Industry/Entity Type
Professional Civil Engineering
Contact Information for Business Card
Name, Position, Address, Cell & Office #, email, and company website
Font styles to use
Other font styles liked:
- Avian
Requirements
Should not have
- No Tools, No Gears, no Cranes, or Construction Equipment.

```html
<!DOCTYPE html>
<html lang="en">
<head>
<meta charset="utf-8">
<title>RW Holloway LLC Business Card</title>
<link href="https://fonts.googleapis.com/css2?family=Montserrat:wght@400;500;700;800&display=swap" rel="stylesheet">
<style>
  :root {
    --backdrop: #1d1d1f;
    --card-white: #ffffff;
    --card-grey-light: #f4f4f5;
    --card-grey-dark: #d9d9dc;
    --orange: #f0922b;
    --blue: #7aaedc;
    --ink: #1c1c1c;
    --edge: #f0922b;
  }
  * { box-sizing: border-box; margin: 0; padding: 0; }
  html, body {
    width: 1200px; height: 900px; overflow: hidden;
    background: var(--backdrop);
    font-family: "Montserrat", sans-serif;
  }
  .canvas {
    width: 1200px; height: 900px;
    display: flex; flex-direction: column; align-items: center; justify-content: center;
    gap: 24px;
  }
  .card {
    position: relative;
    width: 700px; height: 400px;
    border-radius: 28px;
    overflow: hidden;
    box-shadow: 0 3px 0 var(--edge), 0 12px 26px rgba(0,0,0,.5);
  }
  /* front: personal info */
  .card-front {
    background: linear-gradient(135deg, var(--card-grey-light) 0%, #ececee 45%, var(--card-grey-dark) 100%);
  }
  .facet {
    position: absolute; inset: 0;
    background:
      linear-gradient(115deg, transparent 55%, rgba(255,255,255,.35) 55%, rgba(255,255,255,.35) 70%, transparent 70%),
      linear-gradient(30deg, rgba(255,255,255,.4) 0%, transparent 45%);
  }
  .name-block { position: absolute; left: 0; top: 52px; display: flex; align-items: flex-start; }
  .accent-bar { width: 26px; height: 40px; background: var(--orange); margin-right: 22px; }
  .person-name {
    font-weight: 800; font-size: 26px; letter-spacing: .5px;
    color: var(--orange); text-transform: uppercase; line-height: 1.1;
  }
  .person-title { font-size: 18px; color: var(--ink); margin-top: 6px; }
  .brand-mark {
    position: absolute; left: 330px; top: 150px;
    display: flex; align-items: center; gap: 10px;
  }
  .brand-square { width: 14px; height: 14px; background: var(--blue); }
  .brand-name { font-weight: 500; font-size: 24px; color: var(--blue); letter-spacing: 1px; }
  .contact {
    position: absolute; left: 70px; bottom: 44px;
    font-size: 17px; color: var(--ink); line-height: 1.75;
  }
  .contact-row { display: flex; align-items: center; gap: 8px; white-space: nowrap; }
  .contact-row.address { padding-left: 140px; }
  .contact-row.web { padding-left: 130px; }
  .icon { width: 16px; height: 16px; flex: none; }
  .gap { width: 10px; }
  /* back: company name */
  .card-back { background: linear-gradient(160deg, var(--card-white) 0%, #f3f3f4 100%); }
  .back-mark {
    position: absolute; inset: 0;
    display: flex; align-items: center; justify-content: center; gap: 18px;
  }
  .back-square { width: 26px; height: 26px; background: var(--blue); }
  .back-name { font-weight: 500; font-size: 50px; color: var(--blue); letter-spacing: 3px; text-transform: uppercase; }
</style>
</head>
<body>
<main class="canvas">
  <section class="card card-front">
    <div class="facet"></div>
    <div class="name-block">
      <span class="accent-bar"></span>
      <div>
        <p class="person-name">Dana Whitfield</p>
        <p class="person-title">Co-Founder</p>
      </div>
    </div>
    <div class="brand-mark">
      <span class="brand-square"></span>
      <span class="brand-name">RW Holloway LLC</span>
    </div>
    <div class="contact">
      <p class="contact-row address">4120 N. Cedar Road Suite 210 Alder.14</p>
      <p class="contact-row">
        <svg class="icon" viewBox="0 0 16 16"><path fill="var(--orange)" d="M4 1l2.5 3-1.5 2c1 2 2.5 3.5 4.5 4.5l2-1.5 3 2.5-1.5 2.5C7 15 1 9 1.5 2.5z"/></svg>
        555-210-0418
        <span class="gap"></span>
        <svg class="icon" viewBox="0 0 16 16"><rect x="2" y="8" width="12" height="6" rx="1" fill="var(--orange)"/><path d="M1 6c3-4 11-4 14 0l-2 2-2-1.5h-6L3 8z" fill="var(--orange)"/></svg>
        555-210-0362
        <span class="gap"></span>
        <svg class="icon" viewBox="0 0 16 16"><rect x="1" y="3" width="14" height="10" fill="var(--orange)"/><path d="M1 3l7 6 7-6" stroke="#fff" stroke-width="1.4" fill="none"/></svg>
        info@rwhollowayllc
      </p>
      <p class="contact-row web">
        <svg class="icon" viewBox="0 0 16 16"><circle cx="8" cy="8" r="7" fill="var(--orange)"/><path d="M1 8h14M8 1c-3 4-3 10 0 14M8 1c3 4 3 10 0 14" stroke="#fff" stroke-width="1" fill="none"/></svg>
        www.rwhollowaycivil.com
      </p>
    </div>
  </section>

  <section class="card card-back">
    <div class="back-mark">
      <span class="back-square"></span>
      <span class="back-name">RW Holloway LLC</span>
    </div>
  </section>
</main>
</body>
</html>
```